Kelvor Engineers: Why you should hire us keepsake

New design. Open to plastic cards. We are an engineering firm that designs cell phone towers and commercial buildings. Please check out our website www.kelvorstruct.com for more details. We want people to remember our card and for it to be useful if possible. We want the same look and feel on these cards to be translated to other marketing material we may need such as brochures.

Target Market(s)

Architects, Developers and Telecommunication Carriers

Industry/Entity Type

Engineering

Contact Information for Business Card

Card with our company colors, logo, and innovative design with elements related to our industry.

Font styles to use
Sans Serif

Colors
9bcb3c
abd036
0255a3

Requirements
Must have
• Sleek and hip design
Nice to have
• Bright lime green and navy coloring that pops with an innovative design.
Should not have
• A basic and boring design

```html
<!DOCTYPE html>
<html lang="en">
<head>
<meta charset="utf-8">
<title>Kelvor Engineers – Business Card</title>
<link rel="stylesheet" href="https://fonts.googleapis.com/css2?family=Montserrat:wght@500;600;700;800&display=swap">
<style>
  :root {
    --page-bg: #e4e2df;
    --navy-deep: #141b33;
    --navy: #1f2a4c;
    --lime: #35e21c;
    --lime-light: #5cf23c;
    --lime-dark: #22b812;
    --ink-light: #d9d6e0;
    --ink-muted: #b8b3b0;
    --city: #e8b0a2;
    --divider: #8a7f86;
  }
  * { margin: 0; padding: 0; box-sizing: border-box; }
  html, body {
    width: 1200px;
    height: 969px;
    overflow: hidden;
    background: var(--page-bg);
    font-family: "Montserrat", sans-serif;
  }
  .card {
    position: absolute;
    left: 75px;
    top: 170px;
    width: 1050px;
    height: 630px;
    border-radius: 6px;
    overflow: hidden;
    background: linear-gradient(160deg, var(--navy) 0%, var(--navy-deep) 70%);
    box-shadow: 0 18px 40px rgba(0,0,0,0.25);
  }
  .card-band {
    position: absolute;
    inset: 0;
    width: 1050px;
    height: 630px;
  }
  .holder-name {
    position: absolute;
    right: 38px;
    top: 44px;
    font-size: 29px;
    font-weight: 600;
    letter-spacing: 2px;
    color: var(--ink-muted);
    text-transform: uppercase;
  }
  .brand-name {
    position: absolute;
    left: 54px;
    top: 262px;
    font-size: 104px;
    font-weight: 800;
    line-height: 1;
    letter-spacing: -2px;
    color: var(--lime);
  }
  .contact-list {
    position: absolute;
    left: 56px;
    top: 418px;
    list-style: none;
  }
  .contact-list li {
    display: flex;
    align-items: center;
    height: 34px;
    font-size: 21px;
    font-weight: 500;
    color: var(--ink-light);
    white-space: nowrap;
  }
  .contact-icon {
    width: 18px;
    height: 18px;
    margin-right: 14px;
    flex: none;
    fill: var(--ink-muted);
  }
  .website {
    position: absolute;
    left: 56px;
    top: 526px;
    font-size: 21px;
    font-weight: 700;
    letter-spacing: 0.5px;
    color: var(--ink-muted);
    white-space: nowrap;
  }
  .divider {
    position: absolute;
    left: 424px;
    top: 420px;
    width: 2px;
    height: 134px;
    background: var(--divider);
  }
  .office-list {
    position: absolute;
    left: 442px;
    top: 418px;
    list-style: none;
  }
  .office-list li {
    height: 34px;
    display: flex;
    align-items: center;
    font-size: 23px;
    font-weight: 600;
    color: var(--city);
    white-space: nowrap;
  }
  .office-list .dot {
    display: inline-block;
    width: 7px;
    height: 7px;
    border-radius: 50%;
    background: var(--city);
    margin-right: 10px;
  }
  .office-list .dot.inline { margin-left: 12px; }
  .discipline {
    position: absolute;
    left: 442px;
    top: 526px;
    font-size: 23px;
    font-weight: 700;
    letter-spacing: 1px;
    color: var(--ink-muted);
    text-transform: uppercase;
    white-space: nowrap;
  }
</style>
</head>
<body>
  <article class="card" aria-label="Kelvor Engineers business card">
    <svg class="card-band" viewBox="0 0 1050 630" role="img" aria-label="Diagonal lime band with a fine triangular grid pattern">
      <defs>
        <linearGradient id="bandShine" x1="0" y1="0" x2="1" y2="1">
          <stop offset="0" stop-color="#22b812"/>
          <stop offset="0.35" stop-color="#5cf23c"/>
          <stop offset="0.6" stop-color="#35e21c"/>
          <stop offset="1" stop-color="#22b812"/>
        </linearGradient>
      </defs>
      <polygon points="0,0 449,0 1050,344 1050,615 0,27" fill="url(#bandShine)"/>
    </svg>

    <h1 class="holder-name">Dana Whitlow Merce</h1>

    <div class="brand-name">Kelvor</div>

    <ul class="contact-list">
      <li>
        <svg class="contact-icon" viewBox="0 0 20 20" aria-hidden="true"><path d="M5 1l3 4-2 2c1 3 3 5 6 6l2-2 4 3-2 4C8 18 2 12 1 3z"/></svg>
        555.014.2203
      </li>
      <li>
        <svg class="contact-icon" viewBox="0 0 20 20" aria-hidden="true"><path d="M5 0h10a1 1 0 0 1 1 1v18a1 1 0 0 1-1 1H5a1 1 0 0 1-1-1V1a1 1 0 0 1 1-1zm1 3v12h8V3zm4 13.5a1 1 0 1 0 0 2 1 1 0 0 0 0-2z"/></svg>
        555.019.4471
      </li>
      <li>
        <svg class="contact-icon" viewBox="0 0 20 20" aria-hidden="true"><path d="M1 4h18v12H1zm1 1l8 6 8-6z"/></svg>
        dmerce@kelvorstruct.com
      </li>
    </ul>
    <div class="website">WWW.KELVORSTRUCT.COM</div>

    <div class="divider"></div>

    <ul class="office-list">
      <li><span class="dot"></span>Atlanta</li>
      <li><span class="dot"></span>Charlotte</li>
      <li><span class="dot"></span>Houston<span class="dot inline"></span>San Antonio</li>
    </ul>
    <div class="discipline">Multi-Discipline Engineering</div>
  </article>
</body>
</html>
```